QRV Advisors needs a web site

We need a web site for www.qrvadvisors-example.com. QRV is a mergers and acquisition consulting company that focuses our buyer and seller services on logistics companies. We help put companies together, and help with legal and financial due diligence. We want the web site to express our service and show the logistics components. We want personalized images versus pictures of trucks and airplanes.

Our new logo uses Burgandy and grey colors. Image attached. We are not in to bold, big letters...classy, artistic, low key preferred. Confidentiality, experience, professional are what we want to express on the site.

All we expect for the first part of this project is a home page, and one subpage.  We are budgeting other funds for the technical aspects of the web site

Reason: All that I'm seeing so far is trucks, forklifts and planes. We are a legal mergers and acquisitions firm that focus on logistics. I like some of the images to say logistics, but really want it say legal, financial, and putting companies together. Will pay extra for the sub page if someone can impress us with a home page.

Reason: Swamped with another project at the moment...will work on this over the weekend and provide designer feedback and select final design by Tuesday

```html
<!DOCTYPE html>
<html lang="en">
<head>
<meta charset="utf-8">
<title>QRV Advisors — Home</title>
<link href="https://fonts.googleapis.com/css2?family=Ubuntu:wght@400;500;700&family=Open+Sans:wght@400;600;700&display=swap" rel="stylesheet">
<style>
:root{
  --burgundy:#a3093b;
  --burgundy-dark:#86062f;
  --footer:#a80f3f;
  --ink:#3d3d3d;
  --grey:#555;
  --light:#f2f2f2;
  --line:#c9c9c9;
}
*{margin:0;padding:0;box-sizing:border-box}
html,body{width:1063px;height:1200px;overflow:hidden}
body{position:relative;background:#fff;font-family:'Open Sans',sans-serif;color:var(--ink)}
.abs{position:absolute}
.top-band{left:0;top:0;width:1063px;height:407px;background:linear-gradient(#f7f7f7,#e6e6e6)}
.brand{left:141px;top:38px;font-family:'Ubuntu',sans-serif;font-weight:500;font-size:40px;color:var(--burgundy);letter-spacing:1px;display:flex;align-items:center;gap:12px}
.brand .mark{width:14px;height:14px;background:var(--burgundy)}
.call{right:143px;top:43px;font-family:'Ubuntu',sans-serif;font-size:17px;color:var(--grey);display:flex;align-items:center;gap:6px}
.call b{font-weight:500;color:var(--ink)}
.nav{left:141px;top:105px;width:780px;height:34px;background:var(--burgundy);border-radius:3px;box-shadow:0 0 0 2px #d9d9d9}
.nav a{position:absolute;top:10px;font-family:'Ubuntu',sans-serif;font-weight:500;font-size:12px;color:#fff;text-decoration:none;letter-spacing:.2px}
.nav a.active{top:4px;left:9px;width:63px;height:24px;background:#fff;color:#777;border-radius:2px;text-align:center;line-height:24px}
.hero{left:137px;top:151px;width:788px;height:314px;background:#fff;border-radius:4px;box-shadow:0 6px 10px rgba(0,0,0,.18)}
.hero-img{left:141px;top:155px;width:780px;height:306px;border-radius:3px;background:linear-gradient(90deg,#c9cfd6 0%,#e9e6e2 35%,#d5dbe2 55%,#bfc6cf 100%)}
.caption{left:149px;top:432px;height:26px;width:602px;background:rgba(163,9,59,.92);border-radius:3px;color:#fff;font-family:'Ubuntu',sans-serif;font-weight:700;font-size:14.5px;line-height:26px;padding-left:9px;letter-spacing:.2px}
.hero-tabs{left:761px;top:432px;width:107px;height:29px;background:#f4f4f4;border-radius:6px 6px 0 0;display:flex}
.hero-tabs span{flex:1;display:flex;align-items:center;justify-content:center;border-right:1px solid #ddd}
.panel{background:linear-gradient(#f1f1f1,#fff 60%);border:1px solid #e4e4e4;border-radius:2px}
.panel h2{font-family:'Ubuntu',sans-serif;font-weight:400;font-size:18.5px;color:var(--grey)}
.panel h2 em{font-style:normal;color:var(--burgundy)}
.welcome{left:139px;top:490px;width:508px;height:187px}
.welcome h2{position:absolute;left:12px;top:6px}
.rule{position:absolute;height:2px;background:var(--burgundy)}
.welcome p{position:absolute;left:12px;width:482px;font-size:10.3px;line-height:15px;letter-spacing:.3px;color:#333}
.more{position:absolute;font-size:10.5px;color:var(--burgundy);text-decoration:underline}
.news{left:674px;top:490px;width:249px;height:187px}
.news h2{position:absolute;left:12px;top:7px}
.date{position:absolute;left:13px;width:37px;height:37px;text-align:center;font-family:'Ubuntu',sans-serif;border-radius:2px;overflow:hidden}
.date .m{display:block;background:var(--burgundy);color:#fff;font-size:10.5px;font-weight:500;height:16px;line-height:16px}
.date .d{display:block;background:#ddd;color:#333;font-size:14.5px;font-weight:700;height:21px;line-height:21px}
.news h3{position:absolute;font-size:11.5px;font-weight:600;color:var(--burgundy);letter-spacing:.2px}
.news p{position:absolute;font-size:10px;line-height:13.5px;color:#666;letter-spacing:.2px}
.dots{position:absolute;left:14px;width:223px;border-top:1px dotted #3b3b7a}
.card{top:697px;width:244px}
.card .img{position:absolute;left:0;top:0;width:244px;height:133px}
.card .bar{position:absolute;left:0;top:133px;width:244px;height:25px;background:var(--burgundy);color:#fff;font-family:'Ubuntu',sans-serif;font-weight:500;font-size:15px;line-height:26px;padding-left:19px;box-shadow:0 5px 6px rgba(0,0,0,.15)}
.card .go{position:absolute;right:0;top:0;width:33px;height:25px;background:#5a5a5a;display:flex;align-items:center;justify-content:center}
.card p{position:absolute;left:7px;top:174px;width:235px;font-size:10.3px;line-height:16.2px;color:#333}
.card ul{position:absolute;left:14px;top:175px;list-style:none;font-size:10.3px;line-height:16.3px;color:#333}
.card li::before{content:"»";font-size:9px;margin-right:8px}
.card .more{top:237px;right:3px}
.newsletter{left:139px;top:963px;width:784px;height:36px;border:1px solid #ddd;background:linear-gradient(#fafafa,#eee)}
.nl-tag{position:absolute;left:-1px;top:-1px;height:36px}
.nl-tag span{position:absolute;left:34px;top:7px;font-family:'Ubuntu',sans-serif;font-weight:500;font-size:16.5px;color:#fff;white-space:nowrap}
.nl-text{position:absolute;left:207px;top:11px;font-size:10.3px;font-weight:700;color:#333}
.nl-input{position:absolute;left:546px;top:7px;width:162px;height:20px;border:1px solid #bbb;background:#e0e0e0;font-size:10.5px;color:#444;padding-left:8px;line-height:18px}
.nl-submit{position:absolute;left:717px;top:7px;width:58px;height:20px;background:#5a5a5a;color:#fff;font-family:'Ubuntu',sans-serif;font-weight:500;font-size:11.5px;text-align:center;line-height:20px}
.footer{left:0;top:1015px;width:1063px;height:185px;background:var(--footer);border-top:3px solid #8c0a34;color:#fff}
.footer h4{position:absolute;font-family:'Ubuntu',sans-serif;font-weight:500;font-size:13.5px;padding-bottom:4px;border-bottom:1px solid rgba(255,255,255,.25)}
.quick{position:absolute;left:144px;top:45px;list-style:none;font-size:10.3px;font-weight:700;line-height:17.4px}
.map{position:absolute;left:247px;top:42px;width:187px;height:116px;background:linear-gradient(135deg,#e8e6df,#d9d7cf);border:2px solid #fff}
.contact{position:absolute;left:459px;font-size:11.5px;display:flex;gap:8px;line-height:14px}
.contact svg{flex:none;margin-top:1px}
.follow{position:absolute;left:760px;top:23px;font-family:'Ubuntu',sans-serif;font-weight:500;font-size:14px;display:flex;align-items:center;gap:9px}
.follow i{display:block;width:23px;height:23px;background:#d9d9d9;border-radius:3px;border:1px solid #fff}
.foot-brand{position:absolute;left:682px;top:78px;width:242px;text-align:center;font-family:'Ubuntu',sans-serif;font-weight:500;font-size:30px;color:#f3dbe3;letter-spacing:1px}
.copy{position:absolute;left:682px;top:128px;width:242px;text-align:center;font-size:11.5px;line-height:14.5px}
</style>
</head>
<body>
<div class="abs top-band"></div>

<header>
  <div class="abs brand"><span class="mark"></span>QRV Advisors</div>
  <div class="abs call">
    <svg width="20" height="20" viewBox="0 0 20 20"><circle cx="10" cy="10" r="8.5" fill="none" stroke="#a3093b" stroke-width="1.6"/><path d="M8 5c-2 1-2 9 0 10l1.3-1.5-1-2.5 1-2.5L8 5z" fill="#a3093b"/></svg>
    Call us <b>(555) 014-2290</b>
  </div>
  <nav class="abs nav">
    <a class="active" href="#">HOME</a>
    <a style="left:103px" href="#">ABOUT US</a>
    <a style="left:203px" href="#">BUYER SERVICES</a>
    <a style="left:340px" href="#">SELLER SERVICES</a>
    <a style="left:478px" href="#">NEWS &amp; EVENTS</a>
    <a style="left:613px" href="#">FAQ's</a>
    <a style="left:687px" href="#">CONTACT US</a>
  </nav>
</header>

<section>
  <div class="abs hero"></div>
  <div class="abs hero-img" role="img" aria-label="Photo of a smiling team of business professionals in suits"></div>
  <div class="abs caption">QRV Services Are Offered By Industry Executives With Extensive M&amp;A Experience</div>
  <div class="abs hero-tabs">
    <span><svg width="22" height="10"><path d="M1 1l10 8 10-8" fill="none" stroke="#999" stroke-width="1.3"/></svg></span>
    <span style="border:none"><svg width="22" height="10"><path d="M1 9l10-8 10 8" fill="none" stroke="#999" stroke-width="1.3"/></svg></span>
  </div>
</section>

<section class="abs panel welcome">
  <h2>Welcome to QRV <em>Advisors</em></h2>
  <div class="rule" style="left:12px;top:36px;width:460px"></div>
  <p style="top:48px">QRV assists business owners within the logistics industry to implement growth and exit strategies. We offer business planning and merger and acquisition(M&amp;A) advisory services. QRV services are offered by industry executives with extensive M&amp;A experience. Your company will benefit from a unique and outside perspective from consultants that understand your business.</p>
  <p style="top:130px">QRV can help you formulate and execute your growth strategy. We take a strategic and consultative approach with our advisory services ...</p>
  <a class="more" style="right:17px;top:168px" href="#">Read More »</a>
</section>

<section class="abs panel news">
  <h2>News/Events</h2>
  <div class="rule" style="left:12px;top:36px;width:224px"></div>
  <div class="date" style="top:50px"><span class="m">MAR</span><span class="d">29</span></div>
  <h3 style="left:66px;top:44px">Duis aute irure&nbsp; reprehenderit</h3>
  <p style="left:66px;top:62px">Lorem&nbsp;&nbsp; consectetur adipiscing elit.<br>Morbi&nbsp; tristique sem.</p>
  <div class="dots" style="top:101px"></div>
  <div class="date" style="top:109px"><span class="m">APR</span><span class="d">01</span></div>
  <h3 style="left:68px;top:105px">Duis aute irure&nbsp; reprehenderit</h3>
  <p style="left:68px;top:123px">Lorem&nbsp;&nbsp; consectetur adipiscing elit.<br>Morbi&nbsp; tristique sem.</p>
  <div class="dots" style="top:161px"></div>
  <a class="more" style="right:19px;top:168px" href="#">Read More »</a>
</section>

<section>
  <article class="abs card" style="left:142px">
    <div class="img" role="img" aria-label="Photo of business partners shaking hands at a meeting" style="background:linear-gradient(90deg,#d8d4cf,#eeeae6,#c6cbd1)"></div>
    <div class="bar">What We Do<span class="go"><svg width="11" height="10"><path d="M0 3.5h5V0l6 5-6 5V6.5H0z" fill="#fff"/></svg></span></div>
    <p>Lorem&nbsp; consectetur adipiscing elit. Morbi tristique sem. Nunc nec ipsum sed nisi Morbi tristique sem.Lorem consectetur adipiscing elit&nbsp; consectetur adi pis cing elit.</p>
    <a class="more" href="#">Read More »</a>
  </article>
  <article class="abs card" style="left:406px">
    <div class="img" role="img" aria-label="Photo of colleagues reviewing documents around a table" style="background:linear-gradient(90deg,#cfd3d8,#ecebe8,#b9bfc7)"></div>
    <div class="bar">Our Services<span class="go"><svg width="11" height="10"><path d="M0 3.5h5V0l6 5-6 5V6.5H0z" fill="#fff"/></svg></span></div>
    <ul><li>Business Analysis</li><li>Business Intelligence</li><li>Mergers</li><li>Acquisition</li></ul>
    <a class="more" href="#">Read More »</a>
  </article>
  <article class="abs card" style="left:671px">
    <div class="img" role="img" aria-label="Illustration of figures walking through a grey maze" style="background:linear-gradient(160deg,#9a9a9a,#d4d4d4 50%,#8e9aa0)"></div>
    <div class="bar">Our Mission<span class="go"><svg width="11" height="10"><path d="M0 3.5h5V0l6 5-6 5V6.5H0z" fill="#fff"/></svg></span></div>
    <p>Lorem&nbsp; consectetur adipiscing elit. Morbi tristique sem. Nunc nec ipsum sed nisi Morbi tristique sem.Lorem&nbsp; consectetur adipiscing elit consectetur ad ipis cing elit.</p>
    <a class="more" href="#">Read More »</a>
  </article>
</section>

<section class="abs newsletter">
  <div class="nl-tag">
    <svg width="198" height="36"><path d="M0 0h184l13 18-13 18H0z" fill="#a3093b"/>
      <g fill="none" stroke="#fff" stroke-width="1.6"><path d="M19 12h-7v15h13v-6"/><path d="M17 22l2-5 8-8 3 3-8 8z"/></g></svg>
    <span>Newsletter Signup</span>
  </div>
  <div class="nl-text">Lorem ipsum doloronsectetur adipiscing elit. Morbi id tristique.</div>
  <div class="nl-input">Email address</div>
  <div class="nl-submit">SUBMIT</div>
</section>

<footer class="abs footer">
  <h4 style="left:142px;top:21px;width:88px">Quick Link</h4>
  <ul class="quick"><li>Home</li><li>About Us</li><li>Buyer Services</li><li>Seller Services</li><li>News &amp; Events</li><li>FAQ's</li><li>Contact us</li></ul>
  <h4 style="left:247px;top:21px;width:178px">QRV Locations</h4>
  <div class="map" role="img" aria-label="Street map showing the office location"></div>
  <h4 style="left:455px;top:21px;width:150px">Contact Us</h4>
  <div class="contact" style="top:50px"><svg width="16" height="14"><path d="M1 7l7-6 7 6M3 6v7h10V6" fill="none" stroke="#fff" stroke-width="1.6"/></svg><span>Lorem consectetur adipiscing<br>elit. Morbi tristique sem.</span></div>
  <div class="contact" style="top:90px"><svg width="16" height="16"><circle cx="8" cy="8" r="7" fill="none" stroke="#fff" stroke-width="1.3"/><path d="M6.5 4c-1.6 1-1.6 7 0 8l1-1.2-.7-2.3.7-2.3z" fill="#fff"/></svg><span>(555) 014-2290</span></div>
  <div class="contact" style="top:118px"><svg width="16" height="15"><rect x="4" y="1" width="8" height="4" fill="#fff"/><rect x="1" y="5" width="14" height="6" rx="1" fill="#fff"/><rect x="4" y="9" width="8" height="5" fill="#fff" stroke="#a80f3f"/></svg><span>(555) 014-2290</span></div>
  <div class="contact" style="top:148px"><svg width="16" height="12"><rect x="1" y="1" width="14" height="10" fill="none" stroke="#fff" stroke-width="1.3"/><path d="M1 1l7 6 7-6" fill="none" stroke="#fff" stroke-width="1.3"/></svg><span>info@qrvadvisors-example.com</span></div>
  <div class="follow">Follow Us:<i></i><i></i><i></i></div>
  <div class="foot-brand">QRV Advisors</div>
  <div class="copy">© 2014 QRV ADVISORS.<br>All rights reserved.</div>
</footer>
</body>
</html>
```